Buch-/eBook-Cover für Geschichte zum Pride auf Gran Canaria
Zielgruppe
Zielgruppe: Reisefreudige junge schwule Männer
Aufgabenstellung
Die Geschichte spielt zum Pride auf Gran Canaria. Es geht um vier Freunde die dort ihre Ferien verbingen.
Ich stelle mir vor, dass auf dem Cover die Regenbogenflagge ist, Strand, Meer, keine Menschen und ein fetter Schriftzug mit dem Titel #TorvilenaGlanz. Daneben sollte kleiner mein Name Ferdinand zu Brakwede stehen. Das Cover kann aber auch gern wie ein Partyflyer designt sein und der Titel wie ein Logo wirken.
Bin aber für alternativen offen.

```html
<!DOCTYPE html>
<html lang="de">
<head>
<meta charset="utf-8">
<title>#TorvilenaGlanz – Ferdinand zu Brakwede</title>
<link rel="stylesheet" href="https://fonts.googleapis.com/css2?family=Rubik+Dirt&family=Russo+One&display=swap">
<style>
  :root {
    --flag-red: #ef2e3c;
    --flag-orange: #f58a2a;
    --flag-yellow: #f7cf3a;
    --flag-green: #6a9e3a;
    --flag-blue: #1f8fc4;
    --flag-purple: #7a3d8c;
    --sky: #b9dcec;
    --sea: #155c9c;
    --surf: #e9f2f4;
    --sand: #efd3a4;
    --earth: #95705a;
    --title: #fbf8ee;
    --title-glow: rgba(255, 236, 150, 0.9);
    --author: #ffffff;
  }
  html, body {
    margin: 0;
    padding: 0;
    overflow: hidden;
    background: #ffffff;
  }
  .cover {
    position: relative;
    width: 752px;
    height: 1200px;
    overflow: hidden;
  }
  .cover-artwork {
    position: absolute;
    inset: 0;
    width: 752px;
    height: 1200px;
    display: block;
  }
  .cover-title {
    position: absolute;
    top: 212px;
    left: 0;
    width: 752px;
    margin: 0;
    text-align: center;
    font-family: "Rubik Dirt", "Impact", sans-serif;
    font-weight: 400;
    font-size: 78px;
    line-height: 92px;
    letter-spacing: 1px;
    color: var(--title);
    text-transform: uppercase;
    text-shadow:
      2px 3px 0 rgba(60, 60, 40, 0.45),
      0 0 18px var(--title-glow),
      0 0 36px var(--title-glow);
  }
  .cover-title .title-line {
    display: block;
  }
  .cover-author {
    position: absolute;
    top: 1096px;
    left: 0;
    width: 752px;
    margin: 0;
    text-align: center;
    font-family: "Russo One", "Arial Black", sans-serif;
    font-size: 35px;
    line-height: 44px;
    color: var(--author);
    letter-spacing: 0.5px;
  }
</style>
</head>
<body>
<main class="cover">
  <svg class="cover-artwork" viewBox="0 0 752 1200" role="img"
       aria-label="Illustration: wehende Regenbogenflagge über blauem Himmel, darunter Meer mit Brandung und ein Sandstrand voller bunter Konfetti">
    <defs>
      <linearGradient id="artwork-tones" x1="0" y1="0" x2="0" y2="1">
        <stop offset="0" stop-color="var(--flag-red)"/>
        <stop offset="0.14" stop-color="var(--flag-orange)"/>
        <stop offset="0.24" stop-color="var(--flag-yellow)"/>
        <stop offset="0.33" stop-color="var(--flag-green)"/>
        <stop offset="0.42" stop-color="var(--flag-blue)"/>
        <stop offset="0.50" stop-color="var(--flag-purple)"/>
        <stop offset="0.56" stop-color="var(--sky)"/>
        <stop offset="0.62" stop-color="var(--sea)"/>
        <stop offset="0.67" stop-color="var(--surf)"/>
        <stop offset="0.75" stop-color="var(--sand)"/>
        <stop offset="0.88" stop-color="var(--sand)"/>
        <stop offset="0.93" stop-color="var(--earth)"/>
        <stop offset="1" stop-color="var(--earth)"/>
      </linearGradient>
    </defs>
    <rect width="752" height="1200" fill="url(#artwork-tones)"/>
  </svg>

  <h1 class="cover-title">
    <span class="title-line">#Torvilena</span>
    <span class="title-line">Glanz</span>
  </h1>

  <p class="cover-author">Ferdinand zu Brakwede</p>
</main>
</body>
</html>
```